Build a landing page to promote a service (dialler consultation and support).

We are a call centre consultation firm and we need a landing page to promote a service. The service is Tormalux dialler consultation and support.
If you do not know what Tormalux is, please do some quick "Zorvex" research for more information.
The landing page will be promoted with a paid advertisement, so we want something that is simple, and explains exactly what service we offer.
There are two objectives for the landing page:
1) A "call to action" which directs the user to a contact page, including a form plus all of our contact details.
2) A form for them viewers to enter their details to get a "FREE" quote for their project. This form should be placed on the main page.
Notes:
The call to action will require the viewer to enter their name, email, phone number as well as a description of their request. There will also need to be a drop down menu for the type of quote. This menu should have the following options:
1) Tormalux support
2) Tormalux hosting
3) Tormalux customisation
4) Other
We need 2 pages in total:
1) Main landing page
This is the home page. It will need to clearly indicate our services and our key selling features.
Services:
* Tormalux support
* Tormalux hosting
* Tormalux customisation
Key Selling Features:
* Australian based
* PCI complaint
* 10+ years of dialler and call centre experience
* we run a sister company which is a highly reputable 40 seat call centre, so we know first hand about call centre technology.
The main landing page will have an "about us" section with a few paragraphs about how we got started.
-------------------------------------------------------------------------
2) Contact page
All of our contact details will live on this page, as well as a contact form.
Other notes:
We will be self hosting the landing page.
We already have a domain name.
The design must be clean and incorporate our logo, as well as it's colours. (Logo attached)
We want a fully function HTML landing page, not just a "PSD" design.
The page must be mobile optimised.
Anyone using Tormalux software.

```html
<!DOCTYPE html>
<html lang="en">
<head>
<meta charset="utf-8">
<title>Contact Us – Brindlecall</title>
<link rel="stylesheet" href="https://fonts.googleapis.com/css2?family=Montserrat:wght@500;700&family=Open+Sans:wght@400;600&display=swap">
<style>
  :root {
    --brand-blue: #1a7ec6;
    --brand-teal: #1fb39a;
    --text-dark: #3a3a3a;
    --text-body: #555555;
    --field-border: #9a9a9a;
    --footer-bg: #363636;
    --footer-text: #c4c4c4;
    --social-grey: #a8a8a8;
    --white: #ffffff;
  }
  * { box-sizing: border-box; margin: 0; padding: 0; }
  html, body { width: 1200px; height: 760px; overflow: hidden; background: var(--white); }
  body { font-family: "Open Sans", Arial, sans-serif; color: var(--text-dark); position: relative; }

  .site-header { position: absolute; left: 0; top: 0; width: 1200px; height: 101px; }
  .brand { position: absolute; left: 128px; top: 14px; width: 112px; text-align: center; }
  .brand-mark { display: block; width: 45px; height: 45px; border-radius: 50%; background: var(--brand-blue); margin: 0 auto 3px; }
  .brand-name { font-weight: 600; font-size: 17px; color: var(--brand-blue); letter-spacing: 0.3px; }
  .main-nav a { position: absolute; top: 36px; font-size: 16px; line-height: 22px; color: #555; text-decoration: none; }
  .nav-home { left: 541px; }
  .nav-about { left: 628px; }
  .nav-services { left: 738px; }
  .nav-features { left: 840px; }
  .nav-cta { position: absolute; left: 928px; top: 29px; width: 140px; height: 36px; border-radius: 18px; background: var(--brand-blue); color: var(--white); font-family: "Montserrat", Arial, sans-serif; font-weight: 700; font-size: 13px; display: flex; align-items: center; justify-content: center; gap: 7px; text-decoration: none; }
  .header-rule { position: absolute; left: 0; top: 97px; width: 1200px; height: 4px; background: linear-gradient(90deg, var(--brand-blue), var(--brand-teal)); }

  .section-title { position: absolute; top: 173px; width: 1200px; text-align: center; font-family: "Montserrat", Arial, sans-serif; font-weight: 700; font-size: 32px; line-height: 42px; color: var(--brand-blue); }
  .contact-line { position: absolute; width: 1200px; font-size: 17px; line-height: 24px; color: var(--text-dark); display: flex; justify-content: center; gap: 28px; }
  .contact-line span { display: inline-flex; align-items: center; gap: 6px; }
  .contact-line svg { fill: #444; }
  .address { top: 234px; }
  .reach { top: 267px; }

  .contact-form .field { position: absolute; height: 39px; border: 1px solid var(--field-border); border-radius: 2px; font-size: 12.5px; color: var(--text-body); padding: 0 15px; display: flex; align-items: center; background: var(--white); }
  .field-name { left: 133px; top: 317px; width: 218px; }
  .field-email { left: 372px; top: 317px; width: 218px; }
  .field-phone { left: 610px; top: 317px; width: 219px; }
  .field-type { left: 850px; top: 317px; width: 218px; justify-content: space-between; }
  .contact-form .field-message { left: 133px; top: 378px; width: 935px; height: 127px; align-items: flex-start; padding-top: 15px; }
  .submit-btn { position: absolute; left: 550px; top: 523px; width: 100px; height: 37px; border-radius: 2px; background: linear-gradient(#454545, #1c1c1c); color: var(--white); font-family: "Montserrat", Arial, sans-serif; font-size: 16px; font-weight: 500; display: flex; align-items: center; justify-content: center; border: none; }

  .site-footer { position: absolute; left: 0; top: 640px; width: 1200px; height: 120px; background: var(--footer-bg); }
  .footer-nav { position: absolute; left: 133px; top: 37px; font-size: 11.5px; color: var(--footer-text); }
  .footer-nav a { color: var(--footer-text); text-decoration: none; }
  .footer-nav .sep { margin: 0 9px; }
  .copyright { position: absolute; left: 133px; top: 66px; font-size: 11.5px; color: var(--footer-text); }
  .social { position: absolute; left: 1015px; top: 48px; display: flex; gap: 20px; }
  .social span { width: 16px; height: 16px; border-radius: 50%; background: var(--social-grey); display: block; }
</style>
</head>
<body>
  <header class="site-header">
    <div class="brand"><span class="brand-mark"></span><span class="brand-name">Brindlecall</span></div>
    <nav class="main-nav">
      <a class="nav-home" href="#">Home</a>
      <a class="nav-about" href="#">About Us</a>
      <a class="nav-services" href="#">Services</a>
      <a class="nav-features" href="#">Features</a>
    </nav>
    <a class="nav-cta" href="#">
      <svg width="13" height="10" viewBox="0 0 13 10"><rect width="13" height="10" rx="1.5" fill="#fff"/><path d="M0.5 1 L6.5 5.5 L12.5 1" stroke="#1a7ec6" stroke-width="1.4" fill="none"/></svg>
      CONTACT US
    </a>
    <div class="header-rule"></div>
  </header>

  <main class="contact-section">
    <h1 class="section-title">CONTACT US</h1>
    <p class="contact-line address">
      <span>
        <svg width="9" height="13" viewBox="0 0 9 13"><path d="M4.5 0 A4.5 4.5 0 0 1 9 4.5 C9 7.5 4.5 13 4.5 13 C4.5 13 0 7.5 0 4.5 A4.5 4.5 0 0 1 4.5 0 Z M4.5 2.5 A2 2 0 1 0 4.5 6.5 A2 2 0 1 0 4.5 2.5 Z"/></svg>
        24 Building name, Street name, City Zipcode
      </span>
    </p>
    <p class="contact-line reach">
      <span>
        <svg width="12" height="12" viewBox="0 0 12 12"><path d="M2.5 0.5 L4.5 3 L3.4 4.6 C4.2 6.3 5.7 7.8 7.4 8.6 L9 7.5 L11.5 9.5 L10.3 11.4 C5.3 11.2 0.8 6.7 0.6 1.7 Z"/></svg>
        Phone : 555 014 2738
      </span>
      <span>
        <svg width="15" height="11" viewBox="0 0 15 11"><rect width="15" height="11" rx="1.5"/><path d="M0.6 1 L7.5 6 L14.4 1" stroke="#fff" stroke-width="1.4" fill="none"/></svg>
        Email : info@brindlecall.test
      </span>
    </p>

    <form class="contact-form">
      <div class="field field-name">Name</div>
      <div class="field field-email">Email</div>
      <div class="field field-phone">Phone Number</div>
      <div class="field field-type">For Tormalux support
        <svg width="11" height="6" viewBox="0 0 11 6"><path d="M0 0 H11 L5.5 6 Z" fill="#444"/></svg>
      </div>
      <div class="field field-message">Message</div>
      <button class="submit-btn" type="button">SUBMIT</button>
    </form>
  </main>

  <footer class="site-footer">
    <nav class="footer-nav">
      <a href="#">Home</a><span class="sep">|</span><a href="#">About Us</a><span class="sep">|</span><a href="#">Services</a><span class="sep">|</span><a href="#">Features</a><span class="sep">|</span><a href="#">Contact Us</a>
    </nav>
    <p class="copyright">Copyright &nbsp;©&nbsp; 2018 &nbsp;Brindlecall. &nbsp;&nbsp;All rights reserved</p>
    <div class="social"><span></span><span></span></div>
  </footer>
</body>
</html>
```